Lawn sign for construction company

Would like this to be a very clean and high end design for luxury homes. We need a yard sign designed that includes the company logo, website, phone number and major service offerings (residential and commercial renovations and maintenance)
The company website is brackwellbuilders.com all other contact info is in the attachments
Target Market(s)
Luxury home owners and business owners
Industry/Entity Type
Construction/Home Improvement
Font styles to use
Other font styles liked:
- See company logo and other graphics included for title text fonts. All other fonts can be standard sans serif.
Colors
0054AA
0677BA
7BADD7
CADEEF
E8F1F8
Requirements
Must have
- Clean, easy to read design, would like 2 sided sign. A main sign side and back side which states “free estimates, and includes the website and phone number. Must also match the color scheme of the provided logo and other company images. Dark Navy blue primary color, gray secondary color, and orange as an accent color.
Nice to have
- 2nd sign side very simple design
Should not have
- Too many graphics limit to 1-3 colors

```html
<!DOCTYPE html>
<html lang="en">
<head>
<meta charset="utf-8">
<title>Brackwell Builders – Lawn Sign</title>
<link href="https://fonts.googleapis.com/css2?family=Montserrat:wght@500;600;700;800&display=swap" rel="stylesheet">
<style>
  :root {
    --stage: #b3b2b3;
    --sign-edge: #d5d5d5;
    --sign-dark: #cbcbcb;
    --sign-light: #dcdcdc;
    --navy: #0a0f6b;
    --gray: #6b6b6b;
    --orange: #ec7a12;
  }
  * { margin: 0; padding: 0; box-sizing: border-box; }
  html, body { width: 1200px; height: 1200px; overflow: hidden; }
  body {
    background: var(--stage);
    font-family: "Montserrat", Arial, sans-serif;
    position: relative;
  }
  .sign {
    position: absolute;
    left: 225px;
    width: 749px;
    height: 499px;
    background: var(--sign-edge);
    padding: 14px 13px 13px 17px;
  }
  .sign--front { top: 73px; }
  .sign--back { top: 628px; }
  .sign__panel {
    position: relative;
    width: 100%;
    height: 100%;
    border: 1px solid var(--navy);
    background: linear-gradient(to top left, var(--sign-light) 50%, var(--sign-dark) 50%);
    text-align: center;
  }
  .brand-name {
    position: absolute;
    left: 0; right: 0;
    color: var(--orange);
    font-weight: 800;
    font-size: 44px;
    letter-spacing: 1px;
    line-height: 1;
  }
  .sign--front .brand-name { top: 122px; }
  .sign--back .brand-name { top: 140px; }
  .headline {
    position: absolute;
    top: 291px; left: 0; right: 0;
    color: var(--navy);
    font-weight: 800;
    font-size: 63px;
    line-height: 1;
  }
  .rule {
    position: absolute;
    top: 356px; left: 75px;
    width: 566px; height: 1px;
    background: var(--navy);
  }
  .phone {
    position: absolute;
    top: 356px; left: 0; right: 0;
    display: flex;
    justify-content: center;
    align-items: center;
    gap: 12px;
    color: var(--gray);
    font-weight: 600;
    font-size: 66px;
    letter-spacing: 1px;
    line-height: 1;
  }
  .phone__icon { width: 40px; height: 40px; margin-top: 6px; }
  .website {
    position: absolute;
    top: 426px; left: 0; right: 0;
    color: var(--orange);
    font-weight: 500;
    font-size: 32px;
    line-height: 1;
  }
  .services {
    position: absolute;
    top: 330px; left: 0; right: 0;
    color: var(--gray);
    font-weight: 700;
    font-size: 27px;
    line-height: 28px;
    text-transform: uppercase;
  }
  .services__dot {
    display: inline-block;
    width: 12px; height: 12px;
    background: var(--orange);
    margin: 0 7px;
    vertical-align: 3px;
  }
  .contact-bar {
    position: absolute;
    top: 400px; left: 34px;
    width: 644px; height: 51px;
    background: var(--navy);
    border-radius: 14px;
    color: var(--orange);
    font-weight: 700;
    font-size: 27px;
    line-height: 51px;
  }
</style>
</head>
<body>
  <section class="sign sign--front">
    <div class="sign__panel">
      <p class="brand-name">BRACKWELL BUILDERS</p>
      <h1 class="headline">FREE ESTIMATES</h1>
      <div class="rule"></div>
      <p class="phone">
        <svg class="phone__icon" viewBox="0 0 42 42" aria-hidden="true">
          <path d="M9 6c2-1 4 0 5 2l3 6c1 2 0 3-1 4l-2 2c1 4 5 8 9 9l2-2c1-1 2-2 4-1l6 3c2 1 3 3 2 5l-2 3c-2 2-5 3-9 1C16 36 6 26 4 16c-1-4 0-6 2-8z" fill="var(--orange)"/>
          <path d="M24 4a14 14 0 0 1 14 14M23 10a8 8 0 0 1 9 9M23 15a3 3 0 0 1 4 4" fill="none" stroke="var(--orange)" stroke-width="2" stroke-linecap="round"/>
        </svg>
        800-555-0142
      </p>
      <p class="website">www.brackwellbuilders.com</p>
    </div>
  </section>

  <section class="sign sign--back">
    <div class="sign__panel">
      <p class="brand-name">BRACKWELL BUILDERS</p>
      <p class="services">
        Residential Renovations<span class="services__dot"></span>Commercial<br>
        Renovations<span class="services__dot"></span>Maintenance
      </p>
      <p class="contact-bar">800.555.0142 | www.brackwellbuilders.com</p>
    </div>
  </section>
</body>
</html>
```